Heritage Hollow Business Cards

Require a business card design. <br/><br/>Needs to include logo (either round or long version) plus these details:<br/>Maya Torvell<br/>Heritage Hollow<br/>maya@kelvadtrading.com.au<br/>02 6481 7395<br/>PO Box Glenwarra NSW 2791<br/>www.heritagehollow.com.au<br/><br/>I need in an editable format so that I can create for multiple staff members. <br/><br/>

Target Market(s)

We are an online store selling renovation products to home owners are builders. Looking for a classic classy design.

Industry/Entity Type

Home And Garden

Contact Information for Business Card

Maya Torvell
Heritage Hollow
maya@kelvadtrading.com.au
02 6481 7395
PO Box Glenwarra NSW 2791
www.heritagehollow.com.au

Colors

Designer to choose colors to be used in the design.

Requirements
Must have
• Must include Logo.

```html
<!DOCTYPE html>
<html lang="en">
<head>
<meta charset="utf-8">
<title>Heritage Hollow Business Cards</title>
<link href="https://fonts.googleapis.com/css2?family=Open+Sans:wght@400;600;700&display=swap" rel="stylesheet">
<style>
  :root {
    --canvas: #d4d5d4;
    --paper: #ffffff;
    --burgundy: #8b2032;
    --burgundy-deep: #5e1522;
    --ink-light: #ffffff;
  }
  html, body {
    margin: 0;
    padding: 0;
    width: 1200px;
    height: 914px;
    overflow: hidden;
    background: var(--canvas);
    font-family: "Open Sans", Arial, sans-serif;
  }
  .sheet {
    position: relative;
    width: 1200px;
    height: 914px;
  }
  .card {
    position: absolute;
    left: 305px;
    width: 590px;
    height: 337px;
    box-sizing: border-box;
  }
  .card--front {
    top: 76px;
    background: var(--paper);
  }
  .card--back {
    top: 501px;
    background: var(--burgundy);
    color: var(--ink-light);
  }
  .brand-seal {
    position: absolute;
    left: 193px;
    top: 60px;
    width: 216px;
    height: 216px;
    border: 1.5px solid var(--burgundy);
    border-radius: 50%;
    box-sizing: border-box;
    display: flex;
    align-items: center;
    justify-content: center;
  }
  .brand-name {
    margin: 0;
    color: var(--burgundy);
    font-weight: 600;
    font-size: 27px;
    line-height: 1.05;
    text-align: left;
  }
  .website {
    position: absolute;
    left: 0;
    right: 0;
    top: 305px;
    text-align: center;
    color: var(--burgundy);
    font-size: 16px;
    letter-spacing: 0.2px;
  }
  .person {
    position: absolute;
    right: 34px;
    top: 38px;
    margin: 0;
    font-size: 20px;
    font-weight: 400;
  }
  .person strong { font-weight: 700; }
  .contact {
    position: absolute;
    right: 34px;
    top: 239px;
    margin: 0;
    font-style: normal;
    text-align: right;
    font-size: 16px;
    line-height: 22.5px;
    letter-spacing: 0.2px;
  }
  .brand-mark-faint {
    position: absolute;
    left: 35px;
    top: 272px;
    margin: 0;
    color: var(--burgundy-deep);
    font-weight: 600;
    font-size: 27px;
  }
</style>
</head>
<body>
  <main class="sheet">
    <section class="card card--front" aria-label="Card front">
      <div class="brand-seal">
        <p class="brand-name">Heritage<br>Hollow</p>
      </div>
      <div class="website">www.heritagehollow.com.au</div>
    </section>

    <section class="card card--back" aria-label="Card back">
      <h1 class="person">Maya <strong>TORVELL</strong></h1>
      <address class="contact">
        02 6481 7395<br>
        PO Box Glenwarra NSW 2791<br>
        maya@kelvadtrading.com.au
      </address>
      <p class="brand-mark-faint">Heritage Hollow</p>
    </section>
  </main>
</body>
</html>
```